Glow in the Dark Inks Sales Flyer - Targeted to the music industry

We need help!
We need a creative flyer to tell the music industry about our new, colorful glow in the dark inks that look amazing on T-shirts and concert merchandise.

The flyer will go to merchandising managers for bands around the world. The design needs to be hip and contemporary but not offensive. No f-bombs please! Size is 4” x 6” or 3” x 5”, and will be printed on card stock. Design can be both sides if you want. We expect color but black and white with some fluorescent accents could be cool. Surprise us.
Here’s some copy, and we can fill in the contact info when the design is close to final.

Help your fans get lit with branded T-shirts and merchandise that glows in the dark!

Let our new Starwell Pigments light up your next show!

Call us now –
Updates

Hello Designers.

Please keep in mind that although the thought of glow-in-the-dark may trigger a glowing, green color in your creative minds, StarWell Pigments has a wide variety of colors to bring to offer. So please be sure to show that it's not only green glow we are promoting but we have a wide range of colors that glow (including pink, purple, white that glow blue, blue, green, orange, yellow, etc.)

Thank you!

```html
<!DOCTYPE html>
<html lang="en">
<head>
<meta charset="utf-8">
<title>StarWell Pigments – Glow Inks Flyer</title>
<link href="https://fonts.googleapis.com/css2?family=Tinos:wght@400;700&display=swap" rel="stylesheet">
<style>
  :root {
    --ink-black: #050505;
    --glow-olive: #6d6a1c;
    --glow-red: #8c1420;
    --glow-magenta: #a0187e;
    --text-white: #ffffff;
    --brand-pink: #f7c6e4;
    --word-red: #ff3b3b;
    --word-orange: #ff9a2e;
    --word-yellow: #ffe23a;
    --word-green: #4bea5a;
    --word-cyan: #3fd8ef;
    --word-blue: #4f7dff;
    --word-violet: #b35cff;
    --word-pink: #ff5fc8;
  }
  html, body {
    margin: 0;
    padding: 0;
    overflow: hidden;
    background: var(--ink-black);
  }
  .flyer {
    position: relative;
    width: 800px;
    height: 1200px;
    overflow: hidden;
    background: var(--ink-black);
    font-family: "Tinos", "Times New Roman", serif;
    color: var(--text-white);
  }
  .glow-texture {
    position: absolute;
    inset: 0;
    background:
      radial-gradient(ellipse 300px 280px at 120px 260px, rgba(109,106,28,0.85), transparent 75%),
      radial-gradient(ellipse 260px 360px at 390px 300px, rgba(140,20,32,0.9), transparent 72%),
      radial-gradient(ellipse 320px 420px at 700px 440px, rgba(160,24,126,0.9), transparent 72%),
      radial-gradient(ellipse 220px 200px at 250px 120px, rgba(90,80,20,0.5), transparent 75%),
      radial-gradient(ellipse 500px 300px at 400px 760px, rgba(60,10,40,0.45), transparent 75%);
  }
  .brand-name {
    position: absolute;
    top: 470px;
    left: 0;
    width: 100%;
    margin: 0;
    text-align: center;
    font-weight: 700;
    font-size: 60px;
    letter-spacing: 1px;
    color: var(--brand-pink);
  }
  .tagline {
    position: absolute;
    top: 552px;
    left: 0;
    width: 100%;
    margin: 0;
    text-align: center;
    font-weight: 700;
    font-size: 27px;
  }
  .contact {
    position: absolute;
    left: 0;
    width: 100%;
    text-align: center;
    text-transform: uppercase;
    font-size: 24px;
    line-height: 36px;
    margin: 0;
  }
  .contact-heading { top: 772px; }
  .contact-address { top: 836px; }
  .contact-lines { top: 1002px; }
  .color-range {
    position: absolute;
    top: 1150px;
    left: 0;
    width: 100%;
    margin: 0;
    text-align: center;
    text-transform: uppercase;
    font-size: 23px;
    letter-spacing: 0.5px;
    white-space: nowrap;
  }
  .w-red { color: var(--word-red); }
  .w-orange { color: var(--word-orange); }
  .w-yellow { color: var(--word-yellow); }
  .w-green { color: var(--word-green); }
  .w-cyan { color: var(--word-cyan); }
  .w-blue { color: var(--word-blue); }
  .w-violet { color: var(--word-violet); }
  .w-pink { color: var(--word-pink); }
</style>
</head>
<body>
  <div class="flyer">
    <div class="glow-texture" role="img" aria-label="Grungy glowing ink splatter texture in olive, red and magenta on black"></div>

    <h1 class="brand-name">StarWell Pigments</h1>
    <p class="tagline">Let our new Starwell Pigments light up your next show!</p>

    <p class="contact contact-heading">Contact us at:</p>
    <p class="contact contact-address">418 Comet Way.<br>Orland, California CA. 95963</p>
    <p class="contact contact-lines">Tel: +1 530.555.0147<br>Fax: +1 530. 555.0192<br>Email: sales@starwellpigments.com</p>

    <p class="color-range">
      <span class="w-red">StarWell</span>
      <span class="w-orange">Pigments</span>
      <span class="w-yellow">has</span>
      <span class="w-green">a</span>
      <span class="w-green">wide</span>
      <span class="w-cyan">variety</span>
      <span class="w-blue">of</span>
      <span class="w-blue">colors</span>
      <span class="w-violet">to</span>
      <span class="w-pink">offer.</span>
    </p>
  </div>
</body>
</html>
```